Korvile

I'd like new business card design options. I'll need to provide updated contact info although after the deign is complete. We are in IT, specifically in the data backup, archiving and disaster recovery verticals.

Industry/Entity Type

Business

```html
<!DOCTYPE html>
<html lang="en">
<head>
<meta charset="utf-8">
<title>Korvile Business Card</title>
<link rel="stylesheet" href="https://fonts.googleapis.com/css2?family=Montserrat:wght@800&family=Raleway:wght@400;500;600&display=swap">
<style>
  :root {
    --backdrop: #2a2a2c;
    --card: #1c1d1f;
    --map-tone: #2a2c2f;
    --brand-blue: #1a5fc4;
    --brand-light: #2f8fe0;
    --band-blue: #1556c0;
    --text-light: #e6e8ec;
    --text-muted: #b9bec7;
  }
  * { box-sizing: border-box; margin: 0; padding: 0; }
  html, body { width: 1200px; height: 900px; overflow: hidden; }
  body {
    background: var(--backdrop);
    font-family: "Raleway", sans-serif;
    position: relative;
  }
  .card {
    position: absolute;
    left: 250px;
    width: 700px;
    height: 400px;
    background: var(--card);
    overflow: hidden;
  }
  .card--front { top: 35px; }
  .card--back { top: 465px; }
  .card__band {
    position: absolute;
    left: 0; right: 0; bottom: 0;
    height: 10px;
    background: var(--band-blue);
  }
  .map-area {
    position: absolute;
    left: 90px; top: 10px;
    width: 560px; height: 300px;
    background: radial-gradient(ellipse at center, var(--map-tone) 0%, rgba(42,44,47,0.5) 55%, rgba(28,29,31,0) 80%);
  }
  .brand {
    position: absolute;
    display: flex;
    align-items: center;
  }
  .brand__dot {
    border-radius: 50%;
    background: var(--brand-light);
    flex: none;
  }
  .brand__text { display: flex; flex-direction: column; }
  .brand__name {
    font-family: "Montserrat", sans-serif;
    font-weight: 800;
    color: var(--brand-blue);
    text-transform: uppercase;
    line-height: 1;
  }
  .brand__slogan {
    font-family: "Raleway", sans-serif;
    font-weight: 400;
    color: var(--text-muted);
    line-height: 1;
  }
  .card--front .brand { left: 170px; top: 105px; }
  .card--front .brand__dot { width: 80px; height: 80px; margin-right: 22px; }
  .card--front .brand__name { font-size: 46px; letter-spacing: 10px; }
  .card--front .brand__slogan { font-size: 17px; letter-spacing: 1px; margin-top: 10px; }
  .services {
    position: absolute;
    left: 40px; right: 30px; bottom: 32px;
    color: var(--text-light);
    font-size: 16px;
    font-weight: 500;
    letter-spacing: 0.5px;
    text-transform: uppercase;
  }
  .card--back .brand { left: 45px; top: 150px; }
  .card--back .brand__dot { width: 56px; height: 56px; margin-right: 16px; }
  .card--back .brand__name { font-size: 32px; letter-spacing: 6px; }
  .card--back .brand__slogan { font-size: 13px; letter-spacing: 0.5px; margin-top: 7px; }
  .divider {
    position: absolute;
    left: 375px; top: 110px;
    width: 3px; height: 180px;
    background: var(--band-blue);
  }
  .contact {
    position: absolute;
    left: 400px; top: 118px;
    color: var(--text-light);
  }
  .contact__name {
    font-weight: 600;
    color: var(--brand-blue);
    font-size: 21px;
  }
  .contact__role { font-size: 15px; margin-bottom: 12px; }
  .contact__address { font-size: 15px; line-height: 1.3; margin-bottom: 10px; }
  .contact__list { list-style: none; font-size: 15px; line-height: 1.4; }
  .contact__list li { display: flex; align-items: center; }
  .contact__icon { width: 12px; height: 12px; margin-right: 10px; flex: none; }
</style>
</head>
<body>
  <section class="card card--front">
    <div class="map-area" role="img" aria-label="Faint world map in the background"></div>
    <div class="brand">
      <span class="brand__dot"></span>
      <div class="brand__text">
        <span class="brand__name">Korvile</span>
        <span class="brand__slogan">Backup You Can Trust</span>
      </div>
    </div>
    <p class="services">Online PC Backup - Continuous Server Backup - Data Archiving</p>
    <div class="card__band"></div>
  </section>

  <section class="card card--back">
    <div class="brand">
      <span class="brand__dot"></span>
      <div class="brand__text">
        <span class="brand__name">Korvile</span>
        <span class="brand__slogan">Backup You Can Trust</span>
      </div>
    </div>
    <div class="divider"></div>
    <div class="contact">
      <p class="contact__name">Daniel R. Whitford, Ph.D.</p>
      <p class="contact__role">President, CTO</p>
      <p class="contact__address">427 North Alder Avenue<br>Brookfield, Texas 75214</p>
      <ul class="contact__list">
        <li>
          <svg class="contact__icon" viewBox="0 0 12 12" aria-hidden="true"><path d="M2.5 1 L4.5 1 L5.2 3.5 L4 4.5 Q5 7 7.5 8 L8.5 6.8 L11 7.5 L11 9.5 Q10.5 11 9 11 Q1 10 1 2.5 Q1 1 2.5 1 Z" fill="#2f8fe0"/></svg>
          800.555.0142
        </li>
        <li>
          <svg class="contact__icon" viewBox="0 0 12 12" aria-hidden="true"><rect x="3" y="1" width="6" height="3" fill="#2f8fe0"/><rect x="1" y="4.5" width="10" height="4.5" rx="1" fill="#2f8fe0"/><rect x="3" y="8" width="6" height="3" fill="#2f8fe0"/></svg>
          928.555.0187
        </li>
        <li>
          <svg class="contact__icon" viewBox="0 0 12 12" aria-hidden="true"><g fill="none" stroke="#2f8fe0" stroke-width="1"><circle cx="6" cy="6" r="5"/><ellipse cx="6" cy="6" rx="2.2" ry="5"/><line x1="1" y1="6" x2="11" y2="6"/></g></svg>
          www.korvile.com
        </li>
        <li>
          <svg class="contact__icon" viewBox="0 0 12 12" aria-hidden="true"><g fill="none" stroke="#2f8fe0" stroke-width="1"><rect x="1" y="2.5" width="10" height="7"/><polyline points="1,2.5 6,6.5 11,2.5"/></g></svg>
          daniel.whitford@korvile.com
        </li>
      </ul>
    </div>
    <div class="card__band"></div>
  </section>
</body>
</html>
```